Satchel & Sundial needs new business card design

I need a new business card design. I'm looking for out-of-the-box design which represents the freedom of being a location independent entrepreneur.
I offer coaching, retreats and trips.
I would like to see designs with and without the photo.
Colors I use are black (#000000), green (#25A796) and brown (#D7C38C)
Website satchelandsundial.example

Target Market(s)

location independent entrepreneurs, digital nomads, people looking to swap the 9 to 5 for a lifestyle business

Industry/Entity Type

Business

Contact Information for Business Card

Dorota Falkner
Your Lifestyle Business Coach, Retreat & Trip Leader
http://satchelandsundial.example
hello@satchelandsundial.example
Work from anywhere, live everywhere

Font styles to use
Serif
Sans Serif

Requirements
Must have
• One side should contain only the logo. I would also consider having the "Work from anywhere, live everywhere" on that side too (depending on how it looks)
• Please show both sides on the designs.

```html
<!DOCTYPE html>
<html lang="en">
<head>
<meta charset="utf-8">
<title>Satchel &amp; Sundial — Business Card</title>
<link rel="stylesheet" href="https://fonts.googleapis.com/css2?family=Josefin+Sans:wght@600&family=Lora:ital,wght@0,400;1,400&display=swap">
<style>
  :root {
    --ink: #111111;
    --teal: #25A796;
    --gold: #D7C38C;
    --gold-deep: #C8B277;
    --paper: #FFFFFF;
    --paper-shade: #F1F1F1;
    --backdrop: #E6E6E6;
  }
  * { margin: 0; padding: 0; box-sizing: border-box; }
  html, body {
    width: 1200px;
    height: 576px;
    overflow: hidden;
    background: var(--backdrop);
  }
  .canvas {
    position: relative;
    width: 1200px;
    height: 576px;
  }
  .card {
    position: absolute;
    width: 484px;
    height: 292px;
    border-radius: 8px;
    box-shadow: 0 3px 6px rgba(0, 0, 0, 0.25);
  }
  .card--front {
    left: 82px;
    top: 139px;
    background: linear-gradient(180deg, var(--gold) 0%, var(--gold-deep) 100%);
    display: flex;
    align-items: center;
    justify-content: center;
  }
  .brand-name {
    font-family: "Josefin Sans", sans-serif;
    font-weight: 600;
    font-size: 26px;
    line-height: 1;
    letter-spacing: 2px;
    color: var(--ink);
  }
  .card--back {
    left: 602px;
    top: 138px;
    background: linear-gradient(180deg, var(--paper) 0%, var(--paper-shade) 100%);
    text-align: center;
  }
  .card--back > * {
    position: absolute;
    left: 0;
    right: 0;
  }
  .person-name {
    top: 40px;
    font-family: "Josefin Sans", sans-serif;
    font-weight: 600;
    font-size: 22px;
    line-height: 1;
    letter-spacing: 1px;
    color: var(--ink);
  }
  .person-role {
    top: 74px;
    font-family: "Lora", serif;
    font-style: italic;
    font-size: 13px;
    line-height: 1.2;
    color: var(--teal);
  }
  .contact {
    top: 128px;
    font-family: "Lora", serif;
    font-size: 13px;
    line-height: 27px;
    color: var(--ink);
    list-style: none;
  }
  .social {
    top: 186px;
    display: flex;
    justify-content: center;
    gap: 3px;
  }
  .social span {
    width: 11px;
    height: 11px;
    border-radius: 2px;
    background: var(--gold-deep);
  }
  .motto {
    top: 238px;
    font-family: "Josefin Sans", sans-serif;
    font-weight: 600;
    font-size: 14px;
    line-height: 1;
    letter-spacing: 0.5px;
    color: var(--teal);
  }
</style>
</head>
<body>
<main class="canvas">
  <section class="card card--front" aria-label="Card front">
    <h1 class="brand-name">SATCHEL &amp; SUNDIAL</h1>
  </section>

  <section class="card card--back" aria-label="Card back">
    <h2 class="person-name">DOROTA FALKNER</h2>
    <p class="person-role">Coaching, Retreats &amp; Journeys for Lifestyle Founders</p>
    <ul class="contact">
      <li>hello@satchelandsundial.example</li>
      <li>www.satchelandsundial.example</li>
    </ul>
    <div class="social" aria-hidden="true"><span></span><span></span><span></span></div>
    <p class="motto">WORK FROM ANYWHERE, LIVE EVERYWHERE</p>
  </section>
</main>
</body>
</html>
```